Vorlanta PowerPoint Template

I have a company called Vorlanta, LLC and my company logo is already designed. I need a PowerPoint template that I will be using to pitch potential investors and business partners. This should be a very professional-looking template that leverages the company logo colors and really pops. The company is an AI product research and development company.

```html
<!DOCTYPE html>
<html lang="en">
<head>
<meta charset="utf-8">
<title>Vorlanta Investor Deck Template</title>
<link href="https://fonts.googleapis.com/css2?family=Space+Grotesk:wght@400;500;600;700&family=Lato:wght@400;700&display=swap" rel="stylesheet">
<style>
:root{
  --red:#c4262e;
  --red-bright:#e8141b;
  --ink:#4a4a4a;
  --dark:#454545;
  --grey:#7d7d7d;
  --track:#ececec;
  --paper:#ffffff;
  --canvas:#ffffff;
  --line:#e4e4e4;
  --head:"Space Grotesk",sans-serif;
  --body:"Lato",sans-serif;
}
*{margin:0;padding:0;box-sizing:border-box}
html,body{width:1037px;height:1200px;overflow:hidden;background:var(--canvas)}
.board{position:relative;width:1037px;height:1200px}
.slide{position:absolute;width:466px;height:262px;background:var(--paper);overflow:hidden;box-shadow:0 2px 8px rgba(0,0,0,.12);font-family:var(--body);color:var(--ink)}
.col-l{left:34px}.col-r{left:533px}
.row1{top:28px}.row2{top:317px}.row3{top:611px}.row4{top:900px}
.abs{position:absolute}
.photo{position:absolute}
.side-bar{position:absolute;left:0;top:0;width:23px;height:100%;background:var(--dark)}
.badge{position:absolute;left:8px;top:13px;width:24px;height:24px;border-radius:50%;background:#fff;box-shadow:0 1px 3px rgba(0,0,0,.25);display:flex;align-items:center;justify-content:center}
.badge i{width:13px;height:13px;border-radius:50%;background:var(--red);display:block}
.slide-title{position:absolute;left:41px;top:16px;font-family:var(--head);font-weight:500;font-size:14px;color:var(--ink)}
.slide-title b{color:var(--red);font-weight:500}
.foot-date{position:absolute;left:32px;bottom:7px;font-family:var(--head);font-size:6px;color:var(--ink)}
.foot-page{position:absolute;right:24px;bottom:7px;font-family:var(--head);font-size:6px;color:var(--red)}
.lead{position:absolute;font-size:5.6px;line-height:1.75;color:#333}
/* cover */
.brand{position:absolute;display:flex;align-items:center;gap:6px}
.brand .dot{border-radius:50%;background:var(--red)}
.brand .name{font-family:var(--head);font-weight:600;color:var(--ink);letter-spacing:-.5px}
.social{position:absolute;display:flex;gap:13px}
.social span{width:14px;height:14px;border-radius:50%;background:var(--red)}
/* toc */
.toc-item{position:absolute;left:233px;display:flex;align-items:center;gap:12px}
.toc-item .num{width:29px;height:29px;border-radius:50%;border:2.5px solid var(--red);display:flex;align-items:center;justify-content:center;font-family:var(--head);font-size:11px;color:var(--red);background:#fff}
.toc-item .label{font-family:var(--head);font-size:11.5px;color:#222;font-weight:500}
/* team */
.card{position:absolute;top:70px;width:88px;height:131px;background:#fff;box-shadow:0 1px 4px rgba(0,0,0,.12);text-align:center}
.card .avatar{width:34px;height:34px;border-radius:50%;margin:12px auto 7px;background:linear-gradient(#8a8f96,#3e434a)}
.card .who{font-family:var(--head);font-weight:700;font-size:6.5px;color:#222}
.card .role{font-size:5.5px;color:#333;margin-top:3px}
.card .bio{font-size:4.8px;line-height:1.7;color:#999;margin:5px 5px 0}
.card .links{display:flex;gap:3px;justify-content:center;margin-top:6px}
.card .links span{width:9px;height:9px;border-radius:50%;border:.6px solid #bbb}
.card .links span:first-child{background:var(--red);border-color:var(--red)}
/* services */
.service{position:absolute;top:84px;width:116px;height:116px;border-radius:50%;border:2px solid #fff;box-shadow:0 1px 4px rgba(0,0,0,.2)}
.service-name{position:absolute;top:210px;width:140px;text-align:center;font-size:5.8px;font-weight:700;color:#222}
/* thanks */
.contact{position:absolute;top:148px;display:flex;align-items:center;gap:6px}
.contact .ico{width:20px;height:20px;border-radius:50%;background:var(--red);display:flex;align-items:center;justify-content:center}
.contact .k{font-family:var(--head);font-size:6.5px;color:#333}
.contact .v{font-size:6.8px;color:#222;margin-top:2px}
</style>
</head>
<body>
<main class="board">

  <!-- Cover -->
  <section class="slide col-l row1" style="background:linear-gradient(90deg,#fff 0%,#f6f6f6 100%)">
    <div class="brand" style="left:20px;top:28px">
      <span class="dot" style="width:31px;height:31px"></span>
      <span class="name" style="font-size:27px">Vorlanta</span>
    </div>
    <div class="abs" style="left:23px;top:91px;font-family:var(--head);font-size:10px;color:#444">Welcome to</div>
    <div class="abs" style="left:22px;top:103px;font-family:var(--head);font-weight:600;font-size:30px;color:var(--ink);letter-spacing:-.3px">Vorlanta<span style="color:var(--red)">, LLC</span></div>
    <p class="lead" style="left:23px;top:150px;width:185px;font-size:6.8px;line-height:2">Lorem ipsum dolor sit amet, consectetur adipiscing elit, sed do eiusmod tempor incididunt ut labore et dolore magna aliqua.</p>
    <div class="social" style="left:23px;top:197px"><span></span><span></span><span></span><span></span></div>
    <div class="photo" role="img" aria-label="Team of colleagues gathered around a laptop, tinted red" style="left:242px;top:29px;width:202px;height:202px;border-radius:50%;background:radial-gradient(circle at 50% 45%,#f3a0a4,#e0313a 70%,#c4262e);box-shadow:0 0 0 10px rgba(255,255,255,.8)"></div>
  </section>

  <!-- Table of content -->
  <section class="slide col-r row1">
    <div class="abs" style="left:0;top:0;width:68px;height:100%;background:var(--red)"></div>
    <div class="abs" style="left:22px;top:190px;transform:rotate(-90deg);transform-origin:left top;font-family:var(--head);font-size:14px;color:#fff;white-space:nowrap">Table of Content</div>
    <div class="abs" style="left:24px;bottom:7px;font-family:var(--head);font-size:6px;color:#fff">03 June 2025</div>
    <div class="photo" role="img" aria-label="Smiling businesswoman holding a tablet in an office" style="left:68px;top:0;width:180px;height:100%;background:linear-gradient(100deg,#4b5056 0%,#9aa2ab 35%,#dfe3e8 70%,#c9ced4 100%)"></div>
    <span class="abs" style="right:24px;top:10px;width:16px;height:16px;border-radius:50%;background:var(--red)"></span>
    <div class="toc-item" style="top:24px"><span class="num">I</span><span class="label">Introductions</span></div>
    <div class="toc-item" style="top:69px"><span class="num">II</span><span class="label">About Vorlanta</span></div>
    <div class="toc-item" style="top:114px"><span class="num">III</span><span class="label">Our Services</span></div>
    <div class="toc-item" style="top:159px"><span class="num">IV</span><span class="label">Our Graph</span></div>
    <div class="toc-item" style="top:204px"><span class="num">V</span><span class="label">Contact Us</span></div>
    <div class="foot-page">Page no: 02</div>
  </section>

  <!-- About -->
  <section class="slide col-l row2">
    <div class="side-bar"></div>
    <div class="badge"><i></i></div>
    <h2 class="slide-title">About Vorlanta<b>, LLC</b></h2>
    <p class="lead" style="left:41px;top:58px;width:197px;text-align:justify">Lorem ipsum dolor sit amet, consectetur adipiscing elit, sed do eiusmod tempor incididunt ut labore et dolore magna aliqua. Ut enim ad minim veniam, quis nostrud exercitation ullamco laboris nisi ut aliquip ex ea commodo consequat.</p>
    <p class="lead" style="left:41px;top:124px;width:197px;text-align:justify">Duis aute irure dolor in reprehenderit in voluptate velit esse cillum dolore eu fugiat nulla pariatur. Excepteur sint occaecat cupidatat non proident, sunt in culpa qui officia deserunt mollit anim id est laborum. Ut enim ad minim veniam, quis nostrud exercitation ullamco laboris nisi ut aliquip ex ea commodo consequat. Ut enim ad minim veniam, quis nostrud exercitation ullamco laboris nisi ut aliquip ex ea commodo consequat.</p>
    <span class="abs" style="left:277px;top:60px;width:146px;height:146px;border-radius:50%;background:var(--red)"></span>
    <div class="foot-date">03 June 2025</div>
    <div class="foot-page">Page no: 03</div>
  </section>

  <!-- Introduction -->
  <section class="slide col-r row2">
    <div class="photo" role="img" aria-label="Team meeting around a conference table in a modern office" style="left:0;top:0;width:100%;height:100%;background:linear-gradient(120deg,#5d6a76 0%,#9aa6b1 40%,#4f5c68 75%,#2f3a44 100%)"></div>
    <div class="abs" style="left:0;top:100px;width:100%;height:49px;background:#fff;display:flex;align-items:center;justify-content:center;font-family:var(--head);font-weight:600;font-size:28px;color:var(--ink);letter-spacing:.5px">Introduction</div>
    <div class="foot-date" style="color:var(--red)">03 June 2025</div>
    <div class="foot-page" style="color:#fff">Page no: 04</div>
  </section>

  <!-- Team -->
  <section class="slide col-l row3">
    <div class="side-bar"></div>
    <div class="badge"><i></i></div>
    <h2 class="slide-title">Our <b>Team</b></h2>
    <span class="abs" style="left:133px;top:29px;width:206px;height:206px;border-radius:50%;background:#fdf3f3"></span>
    <div class="card" style="left:38px"><div class="avatar" role="img" aria-label="Portrait of team member"></div><div class="who">RAVI KELLAN</div><div class="role">Founder</div><p class="bio">Sed ut perspiciatis unde omnis iste natus er ror sit voluptatem accusantium dolorea.</p><div class="links"><span></span><span></span><span></span></div></div>
    <div class="card" style="left:140px"><div class="avatar" role="img" aria-label="Portrait of team member"></div><div class="who">TOMAS BRELL</div><div class="role">Founder</div><p class="bio">Itaque earum rerum hic tenetur a sapiente delectus, ut aut reiciendis voluptatibus</p><div class="links"><span></span><span></span><span></span></div></div>
    <div class="card" style="left:241px"><div class="avatar" role="img" aria-label="Portrait of team member"></div><div class="who">MIRA OSTEN</div><div class="role">Founder</div><p class="bio">Sed ut perspiciatis unde omnis iste natus er ror sit volupta tem accusantium</p><div class="links"><span></span><span></span><span></span></div></div>
    <div class="card" style="left:343px"><div class="avatar" role="img" aria-label="Portrait of team member"></div><div class="who">TOMAS BRELL</div><div class="role">Founder</div><p class="bio">Earum rerum hic tenetur a sapiente delectus, ut aut reiciendis voluptatibus</p><div class="links"><span></span><span></span><span></span></div></div>
    <div class="foot-date">03 June 2025</div>
    <div class="foot-page">Page no: 05</div>
  </section>

  <!-- Graph -->
  <section class="slide col-r row3">
    <div class="side-bar"></div>
    <div class="badge"><i></i></div>
    <h2 class="slide-title">Our <b>Graph</b></h2>
    <p class="lead" style="left:41px;top:41px;width:405px;font-size:5.6px;color:#222">Temporibus autem quibusdam et aut officiis debitis aut rerum necessitatibus saepe. Itaque earum rerum hic tenetur a sapiente delectus, ut aut reiciendis voluptatibus maiores alias consequatur aut perferendis doloribus asperiores repellat.</p>
    <svg class="abs" style="left:0;top:0" width="466" height="262" viewBox="0 0 466 262" font-family="Lato, sans-serif" font-size="6.2" fill="#222">
      <g stroke="#e6e6e6" stroke-width=".6">
        <line x1="65" y1="99" x2="423" y2="99"/><line x1="65" y1="124" x2="423" y2="124"/><line x1="65" y1="148" x2="423" y2="148"/><line x1="65" y1="172" x2="423" y2="172"/><line x1="65" y1="197" x2="423" y2="197"/>
      </g>
      <g text-anchor="start"><text x="40" y="102">100%</text><text x="40" y="127">75%</text><text x="40" y="151">50%</text><text x="40" y="175">25%</text><text x="40" y="200">0%</text></g>
      <g fill="var(--track)">
        <rect x="79" y="99" width="18" height="104" rx="4"/><rect x="117" y="99" width="18" height="104" rx="4"/><rect x="154" y="99" width="18" height="104" rx="4"/><rect x="192" y="99" width="18" height="104" rx="4"/><rect x="230" y="99" width="18" height="104" rx="4"/><rect x="267" y="99" width="18" height="104" rx="4"/><rect x="305" y="99" width="18" height="104" rx="4"/><rect x="343" y="99" width="18" height="104" rx="4"/><rect x="381" y="99" width="18" height="104" rx="4"/>
      </g>
      <rect x="79" y="182" width="18" height="21" rx="4" fill="var(--grey)"/>
      <rect x="117" y="153" width="18" height="50" rx="4" fill="var(--red)"/>
      <rect x="154" y="136" width="18" height="67" rx="4" fill="var(--grey)"/>
      <rect x="192" y="143" width="18" height="60" rx="4" fill="var(--red)"/>
      <rect x="230" y="130" width="18" height="73" rx="4" fill="var(--grey)"/>
      <rect x="267" y="123" width="18" height="80" rx="4" fill="var(--red)"/>
      <rect x="305" y="119" width="18" height="84" rx="4" fill="var(--grey)"/>
      <rect x="343" y="116" width="18" height="87" rx="4" fill="var(--red)"/>
      <rect x="381" y="99" width="18" height="104" rx="4" fill="var(--grey)"/>
      <g text-anchor="middle"><text x="88" y="216">2016</text><text x="126" y="216">2017</text><text x="163" y="216">2018</text><text x="201" y="216">2019</text><text x="239" y="216">2020</text><text x="276" y="216">2021</text><text x="314" y="216">2022</text><text x="352" y="216">2023</text><text x="390" y="216">2024</text></g>
    </svg>
    <div class="foot-date">03 June 2025</div>
    <div class="foot-page">Page no: 05</div>
  </section>

  <!-- Services -->
  <section class="slide col-l row4">
    <div class="side-bar"></div>
    <div class="badge"><i></i></div>
    <h2 class="slide-title">Our <b>Services</b></h2>
    <p class="lead" style="left:40px;top:45px;width:405px;color:#222">Temporibus autem quibusdam et aut officiis debitis aut rerum necessitatibus saepe. Itaque earum rerum hic tenetur a sapiente delectus, ut aut reiciendis voluptatibus maiores alias consequatur aut perferendis doloribus asperiores repellat.</p>
    <div class="service" role="img" aria-label="Colleagues discussing a product plan at a meeting table" style="left:41px;background:linear-gradient(160deg,#a9bccb,#3d4d5d)"></div>
    <div class="service" role="img" aria-label="Two colleagues reviewing data on a tablet" style="left:184px;background:linear-gradient(160deg,#9ea3a8,#3f3b38)"></div>
    <div class="service" role="img" aria-label="Consultant presenting a strategy at a laptop" style="left:327px;background:linear-gradient(160deg,#c3ccd6,#55616e)"></div>
    <div class="service-name" style="left:29px">AI-Powered Product Development</div>
    <div class="service-name" style="left:173px">Custom Machine Learning Models</div>
    <div class="service-name" style="left:315px">AI Strategy &amp; Integration Consulting</div>
    <div class="foot-date">03 June 2025</div>
    <div class="foot-page">Page no: 07</div>
  </section>

  <!-- Thank you -->
  <section class="slide col-r row4">
    <div class="photo" role="img" aria-label="Faded photo of a business handshake in an office" style="left:0;top:0;width:100%;height:100%;background:linear-gradient(120deg,#f3f3f3,#e6e7e9 50%,#f5f5f5)"></div>
    <div class="brand" style="left:123px;top:42px;gap:10px">
      <span class="dot" style="width:48px;height:48px"></span>
      <span class="name" style="font-size:38px">Vorlanta</span>
    </div>
    <p class="lead" style="left:30px;top:106px;width:406px;text-align:center;color:#222;font-size:5.8px">Lorem ipsum dolor sit amet, consectetur adipiscing elit, sed do eiusmod tempor incididunt ut labore et dolore magna aliqua. Ut enim ad minim veniam, quis nostrud exercitation ullamco laboris nisi ut aliquip ex ea commodo consequat.</p>
    <div class="contact" style="left:23px">
      <span class="ico"><svg width="9" height="11" viewBox="0 0 9 11"><path d="M4.5 0A4 4 0 0 0 .5 4c0 3 4 7 4 7s4-4 4-7a4 4 0 0 0-4-4z" fill="#fff"/><circle cx="4.5" cy="4" r="1.5" fill="var(--red)"/></svg></span>
      <div><div class="k">LOCATION:</div><div class="v">Vorlanta, United States</div></div>
    </div>
    <div class="contact" style="left:188px">
      <span class="ico"><svg width="10" height="7" viewBox="0 0 10 7"><rect width="10" height="7" rx="1" fill="#fff"/><path d="M0 .5l5 3.3 5-3.3" stroke="var(--red)" stroke-width=".9" fill="none"/></svg></span>
      <div><div class="k">EMAIL US:</div><div class="v">info@vorlanta.com</div></div>
    </div>
    <div class="contact" style="left:347px">
      <span class="ico"><svg width="10" height="10" viewBox="0 0 24 24"><path d="M6.6 10.8a15 15 0 0 0 6.6 6.6l2.2-2.2a1 1 0 0 1 1-.25 11.4 11.4 0 0 0 3.6.6 1 1 0 0 1 1 1V20a1 1 0 0 1-1 1A17 17 0 0 1 3 4a1 1 0 0 1 1-1h3.5a1 1 0 0 1 1 1c0 1.25.2 2.45.6 3.6a1 1 0 0 1-.25 1z" fill="#fff"/></svg></span>
      <div><div class="k">PHONE NUMBER:</div><div class="v">+1 555 014 2290</div></div>
    </div>
    <div class="abs" style="left:0;top:193px;width:100%;text-align:center;font-family:var(--head);font-weight:700;font-size:22px;color:var(--red);letter-spacing:.5px">THANK YOU</div>
  </section>

</main>
</body>
</html>
```